THE WELLNESS BARN WEBSITE for Physio, Fitness, health

An attractive website advertising a physiotherapyand fitness / gym business, not generic, colours are natural, greens, browns, beiges. No cheesy pictures. With the ability to sell a small,amount of goods online if i decide to. Simple to navigate. Text boxes that i can input the main information and change easily. Somewhere to put my timetable. Easy to find contact details. However many pages it needs, im not fussed.
Target Market(s)
People looking for rehabilitation or fitness classes
Industry/Entity Type
Physiotherapy, Fitness, Gym, Health
Coding
Coded - Design and coding required
Number of Pages Required
1 page
Font styles to use
Other font styles liked:
- Im not fusse,ld, not script
Requirements
Must have
- Will upload posts from my business insta page for reference about the feel. Earthy natural tones, I have a lot of timber, and rustic looking piece's, plants etc in my clinic
Nice to have
- Simple to navigate
Should not have
- Cheesy "yoga" or generic "people doing physio" pics

```html
<!DOCTYPE html>
<html lang="en">
<head>
<meta charset="utf-8">
<title>The Wellness Barn Cedar Bay</title>
<link rel="stylesheet" href="https://fonts.googleapis.com/css2?family=Oswald:wght@400;500;600&family=Mulish:wght@400;600;700&display=swap">
<style>
:root{
  --green:#1f3a1e;
  --green-dark:#1a3119;
  --stone:#b1ae9d;
  --cream:#f4f1e9;
  --card:#f3f0e8;
  --ink:#1b1b1b;
  --muted:#555;
  --white:#fff;
  --line:#c9c5b8;
}
*{box-sizing:border-box;margin:0;padding:0}
html,body{width:1200px;height:5159px;overflow:hidden}
body{position:relative;background:var(--white);font-family:'Mulish',sans-serif;color:var(--ink)}
.abs{position:absolute}
.heading{font-family:'Oswald',sans-serif;font-weight:500;text-transform:uppercase;color:var(--ink)}
.section-title{position:absolute;left:0;width:1200px;text-align:center;font-family:'Oswald',sans-serif;font-weight:500;font-size:40px;letter-spacing:.5px}
.rule{position:absolute;left:578px;width:44px;height:4px;background:var(--green)}
.photo{position:absolute}
.btn{position:absolute;display:flex;align-items:center;justify-content:center;font-family:'Oswald',sans-serif;font-weight:500;text-transform:uppercase;background:var(--green);color:var(--white)}
/* header */
.follow{left:148px;top:38px;display:flex;align-items:center;gap:10px;font-family:'Oswald',sans-serif;font-size:12px;font-weight:500}
.dot-icon{width:26px;height:26px;border:2px solid var(--ink);border-radius:50%}
.brand{left:480px;top:18px;width:240px;height:108px;display:flex;align-items:center;justify-content:center;text-align:center;font-family:'Oswald',sans-serif;font-weight:600;font-size:28px;line-height:1.05;color:var(--green);z-index:3}
.call{left:836px;top:26px;display:flex;align-items:center;gap:14px}
.call small{display:block;font-family:'Oswald',sans-serif;font-size:13px;font-weight:500}
.call strong{font-family:'Oswald',sans-serif;font-size:22px;font-weight:500}
.nav{left:0;top:96px;width:1200px;height:48px;background:var(--stone)}
.nav a{position:absolute;top:0;height:48px;line-height:48px;font-family:'Oswald',sans-serif;font-size:15px;color:var(--ink);text-decoration:none;text-transform:uppercase;padding:0 12px}
.nav a.active{background:var(--green);color:var(--white)}
/* hero */
.hero{left:0;top:144px;width:1200px;height:526px;background:linear-gradient(180deg,#6c6b66 0%,#4a4945 45%,#2b2b2a 100%)}
.hero h1{position:absolute;left:148px;top:208px;font-family:'Oswald',sans-serif;font-weight:500;font-size:45px;line-height:57px;color:var(--white)}
.hero .more{left:150px;top:402px;width:136px;height:46px;background:var(--white);color:var(--ink);font-size:17px}
.dots{left:554px;top:476px;display:flex;gap:16px}
.dots i{width:11px;height:11px;border-radius:50%;background:#fff;opacity:.85}
/* services */
.service{position:absolute;width:440px;height:262px;border:1px solid var(--line);background:var(--white)}
.service .photo{top:0;height:100%;width:220px}
.service .panel{position:absolute;width:270px;top:0;height:100%;padding:78px 28px 0 26px;background:var(--white)}
.service h3{font-family:'Oswald',sans-serif;font-weight:500;font-size:20px;line-height:30px;text-transform:uppercase}
.service p{font-size:11px;line-height:17px;color:var(--muted);margin-top:12px}
.service svg{position:absolute;top:24px}
/* offer */
.offer-band{left:0;top:1485px;width:1200px;height:615px;background:var(--stone)}
.offer-photo{left:128px;top:1585px;width:380px;height:380px;border-radius:50%;background:radial-gradient(circle at 50% 30%,#c9cfd2 0%,#8ea07a 55%,#5f7446 100%)}
.offer h2{position:absolute;left:626px;top:1578px;font-family:'Oswald',sans-serif;font-weight:500;font-size:40px;line-height:52px}
.offer p{position:absolute;left:626px;top:1740px;width:424px;font-size:13.5px;line-height:22.5px;color:#2a2a2a}
/* team */
.member{position:absolute;top:2316px;width:282px;height:476px;background:var(--card)}
.member .photo{left:0;top:0;width:282px;height:240px}
.member h3{position:absolute;left:30px;top:262px;font-family:'Oswald',sans-serif;font-weight:500;font-size:19px}
.member .role{position:absolute;left:30px;top:292px;font-size:13px}
.member p{position:absolute;left:30px;top:324px;width:230px;font-size:11px;line-height:18px;color:var(--muted)}
.member .social{position:absolute;left:32px;top:424px;display:flex;gap:8px}
.member .social i{width:26px;height:26px;border-radius:50%;background:var(--green)}
/* testimonials */
.testi-band{left:0;top:2870px;width:1200px;height:730px;background:var(--cream)}
.quote{position:absolute;top:3104px;width:290px;height:386px;background:var(--white);text-align:center}
.quote .marks{margin-top:32px;font-family:'Oswald',sans-serif;font-size:72px;line-height:60px;color:#a9a597}
.quote .stars{margin-top:6px;color:var(--green);font-size:16px;letter-spacing:2px}
.quote p{margin:10px auto 0;width:190px;font-size:13px;line-height:22.5px;color:#333}
.quote .avatar{width:42px;height:42px;border-radius:50%;background:#b59a86;border:2px solid #e6e0d4;margin:22px auto 0}
.quote b{display:block;margin-top:14px;font-size:13px}
.quote small{display:block;margin-top:4px;font-size:11px;color:var(--muted)}
.arrow{position:absolute;width:42px;height:42px;border:1.5px solid #999;border-radius:50%;display:flex;align-items:center;justify-content:center}
/* shop */
.product{position:absolute;top:3790px;width:213px}
.product .photo{position:relative;width:213px;height:212px}
.product h3{margin-top:34px;font-family:'Oswald',sans-serif;font-weight:500;font-size:20px}
.product .price{margin-top:8px;font-size:14px}
.product .price s{font-size:10px;color:#777;margin-left:6px}
.product .buy{position:relative;margin-top:14px;width:80px;height:32px;font-size:12px}
/* faq */
.faq-band{left:0;top:4215px;width:1200px;height:530px;background:var(--stone)}
.faq-intro{left:270px;top:4384px;width:660px;text-align:center;font-size:16px;line-height:27px;color:#2a2a2a}
.faq-item{position:absolute;left:264px;width:672px;height:42px;background:var(--white);display:flex;align-items:center;justify-content:space-between;padding:0 18px;font-family:'Oswald',sans-serif;font-weight:500;font-size:16px}
.plus{width:22px;height:22px;border-radius:50%;background:#a9a597;color:#fff;display:flex;align-items:center;justify-content:center;font-size:18px;line-height:1}
/* footer */
.footer{left:0;top:4745px;width:1200px;height:414px;background:var(--green);color:var(--white)}
.footer .logo{position:absolute;left:150px;top:70px;width:220px;height:160px;display:flex;align-items:center;justify-content:center;text-align:center;font-family:'Oswald',sans-serif;font-weight:600;font-size:32px;line-height:1.1;color:var(--white)}
.footer h4{position:absolute;font-family:'Oswald',sans-serif;font-weight:500;font-size:22px}
.contact-row{position:absolute;left:430px;display:flex;gap:16px;align-items:flex-start;font-size:13px;line-height:20px}
.contact-row .ic{width:30px;height:30px;border-radius:50%;background:#d9d6cb;display:flex;align-items:center;justify-content:center;flex:none}
.footer .news{position:absolute;left:738px;top:98px;width:300px;font-size:13px;line-height:20px}
.footer .email{position:absolute;left:742px;top:170px;width:306px;height:42px;border:2px solid #fff;padding:0 20px;display:flex;align-items:center;font-size:13px}
.footer .sub{position:absolute;left:742px;top:228px;width:306px;height:42px;background:#fff;color:var(--ink);display:flex;align-items:center;justify-content:center;font-family:'Oswald',sans-serif;font-weight:500;font-size:21px}
.footer hr{position:absolute;left:150px;top:315px;width:898px;border:0;border-top:1px solid #5b6f59}
.footer .legal{position:absolute;left:0;top:340px;width:1200px;text-align:center;font-size:11px}
</style>
</head>
<body>

<!-- Header -->
<div class="abs follow">FOLLOW US <span class="dot-icon"></span><span class="dot-icon"></span></div>
<div class="abs brand">THE WELLNESS<br>BARN</div>
<div class="abs call">
  <svg width="32" height="32" viewBox="0 0 24 24" fill="none" stroke="#1b1b1b" stroke-width="1.4"><path d="M5 3h4l2 5-2.5 1.5a11 11 0 0 0 6 6L16 13l5 2v4a2 2 0 0 1-2 2A16 16 0 0 1 3 5a2 2 0 0 1 2-2z"/><path d="M15 3a6 6 0 0 1 6 6M15 7a2 2 0 0 1 2 2"/></svg>
  <div><small>CALL US</small><strong>+61 400 555 219</strong></div>
</div>
<nav class="abs nav">
  <a class="active" style="left:174px">Home</a>
  <a style="left:266px">About Us</a>
  <a style="left:402px">Programs</a>
  <a style="left:704px">Shop</a>
  <a style="left:794px">Testimonials</a>
  <a style="left:944px">Contact</a>
</nav>

<!-- Hero -->
<section class="abs hero" role="img" aria-label="Group of clients training with barbells in the gym">
  <h1>PHYSIO-LED WELLNESS<br>AT THE WELLNESS BARN<br>CEDAR BAY.</h1>
  <div class="btn more">Read More</div>
  <div class="abs dots"><i></i><i></i><i></i><i></i></div>
</section>

<!-- Services -->
<h2 class="section-title" style="top:715px">OUR SERVICES</h2>
<div class="rule" style="top:794px"></div>

<div class="service" style="left:148px;top:860px">
  <div class="photo" role="img" aria-label="Physiotherapist guiding a client through a shoulder stretch" style="left:0;background:linear-gradient(135deg,#8b8f8c,#4d6a76)"></div>
  <div class="panel" style="left:170px">
    <svg style="left:110px" width="50" height="50" viewBox="0 0 48 48" fill="none" stroke="#1f3a1e" stroke-width="2"><circle cx="26" cy="8" r="4"/><path d="M18 20l8-6 6 8M10 34h30v6H10zM22 28h12"/></svg>
    <h3>Physiotherapy<br>Classes for Everyone</h3>
    <p>Our classes are tailored for all ages, focusing on safe movement to enhance mobility and overall health.</p>
  </div>
</div>
<div class="service" style="left:608px;top:860px">
  <div class="photo" role="img" aria-label="Person reaching upward outdoors in the sun" style="left:0;background:linear-gradient(135deg,#b9c3c9,#7d92a3)"></div>
  <div class="panel" style="left:170px">
    <svg style="left:110px" width="50" height="50" viewBox="0 0 48 48" fill="none" stroke="#1f3a1e" stroke-width="2"><path d="M24 6a14 14 0 0 0-10 24v12h12v-6h6a4 4 0 0 0 4-4v-6l4-2-4-6a14 14 0 0 0-12-12z"/><path d="M20 18a3 3 0 0 1 6 0 3 3 0 0 1 6 0c0 4-6 8-6 8s-6-4-6-8z"/></svg>
    <h3>Holistic Wellness<br>Programs</h3>
    <p>Our programs integrate physical activity with nutritional guidance to support sustainable health.</p>
  </div>
</div>
<div class="service" style="left:148px;top:1148px">
  <div class="photo" role="img" aria-label="Person meditating on a timber deck at dusk" style="left:220px;background:linear-gradient(180deg,#9a8f84,#5b4536)"></div>
  <div class="panel" style="left:0">
    <svg style="left:40px" width="50" height="50" viewBox="0 0 48 48" fill="none" stroke="#1f3a1e" stroke-width="2"><circle cx="24" cy="10" r="5"/><path d="M24 16v12M12 26l12-4 12 4M10 40l14-8 14 8M10 40h28"/></svg>
    <h3>Mindfulness and<br>Yoga Sessions</h3>
    <p>Join our yoga sessions to improve mental clarity and physical flexibility in a calming environment.</p>
  </div>
</div>
<div class="service" style="left:608px;top:1148px">
  <div class="photo" role="img" aria-label="Dietitian holding a bowl of fresh vegetables" style="left:220px;background:linear-gradient(135deg,#d6d9d8,#6f8a4a)"></div>
  <div class="panel" style="left:0">
    <svg style="left:40px" width="50" height="50" viewBox="0 0 48 48" fill="none" stroke="#1f3a1e" stroke-width="2"><path d="M6 24h36a18 14 0 0 1-36 0zM12 22c2-8 6-10 12-10s10 2 12 10M20 12l-4-6M28 12l4-6"/></svg>
    <h3>Personalized<br>Nutrition Guidance</h3>
    <p>Receive expert dietary advice tailored to your needs, helping you make informed health choices.</p>
  </div>
</div>

<!-- Offer -->
<svg class="abs" style="left:0;top:1470px" width="1200" height="30" viewBox="0 0 1200 30" preserveAspectRatio="none"><path fill="#b1ae9d" d="M0 30V16l40 6 30-12 50 8 40-10 60 12 50-8 40 6 60-14 50 10 40-6 60 12 50-10 40 8 60-12 50 10 40-8 60 12 50-10 40 6 60-12 50 8 40-6 60 12 50-8 40 4 30-6v18z"/></svg>
<section class="abs offer-band"></section>
<svg class="abs" style="left:0;top:2090px" width="1200" height="34" viewBox="0 0 1200 34" preserveAspectRatio="none"><path fill="#b1ae9d" d="M0 0v18l40-6 30 14 50-10 40 12 60-14 50 8 40-6 60 16 50-10 40 6 60-14 50 10 40-8 60 12 50-10 40 8 60-12 50 10 40-6 60 14 50-8 40 6 30-6V0z"/></svg>
<div class="abs offer-photo" role="img" aria-label="Trainers and client outdoors with a tractor tyre on grass"></div>
<div class="offer">
  <h2>WHAT DO WE HAVE<br>TO OFFER?</h2>
  <div class="abs" style="left:626px;top:1705px;width:44px;height:4px;background:var(--green)"></div>
  <p>The Wellness Barn Cedar Bay is dedicated to empowering individuals to achieve their health and wellbeing goals through safe and effective movement. Our core values include Integrity, Collaboration, Inclusivity, and a strong Commitment to health. We believe in providing professional support tailored to each individual's needs. Our team, including experienced professionals like Dr. Clara Whitfield and Owen Hartley, is committed to guiding you on your wellness journey. Join us in fostering a healthier community where everyone can thrive.</p>
  <div class="btn" style="left:628px;top:1995px;width:138px;height:47px;font-size:17px">Read More</div>
</div>

<!-- Team -->
<h2 class="section-title" style="top:2178px">MEET OUR TEAM</h2>
<div class="rule" style="top:2262px"></div>

<div class="member" style="left:148px">
  <div class="photo" role="img" aria-label="Portrait of the lead physiotherapist in a clinic" style="background:linear-gradient(180deg,#e4e2dc,#b9b3a8)"></div>
  <h3>DR. CLARA WHITFIELD</h3><div class="role">Lead Physiotherapist</div>
  <p>Dr. Clara specializes in sports rehabilitation and has over 10 years of experience in helping clients recover from injuries.</p>
  <div class="social"><i></i><i></i></div>
</div>
<div class="member" style="left:458px">
  <div class="photo" role="img" aria-label="Portrait of the wellness coach seated in a library" style="background:linear-gradient(180deg,#6d6a62,#3a4046)"></div>
  <h3>LEON ASHBY</h3><div class="role">Wellness Coach</div>
  <p>Leon focuses on holistic health and wellness, guiding clients through lifestyle changes to improve their overall wellbeing.</p>
  <div class="social"><i></i><i></i></div>
</div>
<div class="member" style="left:765px">
  <div class="photo" role="img" aria-label="Portrait of the physiotherapy assistant in scrubs" style="background:linear-gradient(180deg,#bdb6a8,#4d6d8a)"></div>
  <h3>NORA VANCE</h3><div class="role">Physiotherapy Assistant</div>
  <p>Nora assists in physiotherapy sessions and is passionate about helping clients achieve their health goals.</p>
  <div class="social"><i></i><i></i></div>
</div>

<!-- Testimonials -->
<svg class="abs" style="left:0;top:2855px" width="1200" height="30" viewBox="0 0 1200 30" preserveAspectRatio="none"><path fill="#f4f1e9" d="M0 30V14l40 8 30-14 50 10 40-8 60 12 50-10 40 6 60-14 50 12 40-6 60 10 50-12 40 8 60-10 50 12 40-8 60 10 50-12 40 8 60-10 50 10 40-6 30-8v22z"/></svg>
<section class="abs testi-band"></section>
<svg class="abs" style="left:0;top:3595px" width="1200" height="30" viewBox="0 0 1200 30" preserveAspectRatio="none"><path fill="#f4f1e9" d="M0 0v16l40-8 30 14 50-10 40 8 60-12 50 10 40-6 60 14 50-12 40 6 60-10 50 12 40-8 60 10 50-12 40 8 60-10 50 12 40-8 60 10 50-10 40 6 30 6V0z"/></svg>
<h2 class="section-title" style="top:2970px">CLIENT SUCCESS STORIES</h2>
<div class="rule" style="top:3056px"></div>
<div class="arrow" style="left:66px;top:3274px"><svg width="14" height="14" viewBox="0 0 14 14"><path d="M9 2L4 7l5 5" fill="none" stroke="#888" stroke-width="1.5"/></svg></div>
<div class="arrow" style="left:1086px;top:3274px"><svg width="14" height="14" viewBox="0 0 14 14"><path d="M5 2l5 5-5 5" fill="none" stroke="#888" stroke-width="1.5"/></svg></div>

<div class="quote" style="left:148px"><div class="marks">&ldquo;</div><div class="stars">★★★★★</div><p>The Wellness Barn has completely changed my approach to fitness. Their programs are tailored and effective!</p><div class="avatar"></div><b>Tessa Morrow</b><small>Fitness Enthusiast</small></div>
<div class="quote" style="left:454px"><div class="marks">&ldquo;</div><div class="stars">★★★★★</div><p>I never thought I could regain my mobility. The physiotherapy classes here are a game changer!</p><div class="avatar"></div><b>Glen Roper</b><small>Retired Veteran</small></div>
<div class="quote" style="left:758px"><div class="marks">&ldquo;</div><div class="stars">★★★★★</div><p>I love how the wellness programs fit into my hectic schedule. I feel healthier and more energetic!</p><div class="avatar"></div><b>Ivy Langford</b><small>Busy Mom</small></div>

<!-- Shop -->
<h2 class="section-title" style="top:3655px">SHOP</h2>
<div class="rule" style="top:3740px"></div>
<div class="arrow" style="left:66px;top:3880px"><svg width="14" height="14" viewBox="0 0 14 14"><path d="M9 2L4 7l5 5" fill="none" stroke="#888" stroke-width="1.5"/></svg></div>
<div class="arrow" style="left:1086px;top:3880px"><svg width="14" height="14" viewBox="0 0 14 14"><path d="M5 2l5 5-5 5" fill="none" stroke="#888" stroke-width="1.5"/></svg></div>

<div class="product" style="left:150px"><div class="photo" role="img" aria-label="Spray bottle among green plants" style="background:linear-gradient(135deg,#5a7040,#2d3a24)"></div><h3>PRODUCT 1</h3><div class="price">$25.99<s>$45.99</s></div><div class="btn buy">Buy Now</div></div>
<div class="product" style="left:377px"><div class="photo" role="img" aria-label="Branded cap and t-shirt" style="background:linear-gradient(135deg,#c9c6bf,#6f6a5d)"></div><h3>PRODUCT 2</h3><div class="price">$25.99<s>$45.99</s></div><div class="btn buy">Buy Now</div></div>
<div class="product" style="left:606px"><div class="photo" role="img" aria-label="Branded drink tumblers with dried flowers" style="background:linear-gradient(135deg,#a08a66,#6e4a4c)"></div><h3>PRODUCT 3</h3><div class="price">$25.99<s>$45.99</s></div><div class="btn buy">Buy Now</div></div>
<div class="product" style="left:834px"><div class="photo" role="img" aria-label="Heat pack and gift box on timber" style="background:linear-gradient(135deg,#d8c4a8,#a4603c)"></div><h3>PRODUCT 4</h3><div class="price">$25.99<s>$45.99</s></div><div class="btn buy">Buy Now</div></div>

<!-- FAQ -->
<svg class="abs" style="left:0;top:4215px" width="1200" height="24" viewBox="0 0 1200 24" preserveAspectRatio="none"><path fill="#fff" d="M0 0h1200v2c-30 0-30 18-60 18s-30-18-60-18-30 18-60 18-30-18-60-18-30 18-60 18-30-18-60-18-30 18-60 18-30-18-60-18-30 18-60 18-30-18-60-18-30 18-60 18-30-18-60-18-30 18-60 18-30-18-60-18-30 18-60 18-30-18-60-18-30 18-60 18-30-18-60-18-30 18-60 18-30-18-60-18-30 18-60 18S30 2 0 2z"/></svg>
<section class="abs faq-band"></section>
<h2 class="section-title" style="top:4262px">FAQS</h2>
<div class="rule" style="top:4342px"></div>
<p class="abs faq-intro">Find answers to common questions about our health and wellness programs, services, and how we can support your journey to better health.</p>
<div class="faq-item" style="top:4470px">WHAT TYPES OF PROGRAMS DO YOU OFFER?<span class="plus">+</span></div>
<div class="faq-item" style="top:4524px">HOW CAN I GET STARTED?<span class="plus">+</span></div>
<div class="faq-item" style="top:4578px">ARE YOUR CLASSES SUITABLE FOR BEGINNERS?<span class="plus">+</span></div>
<div class="btn" style="left:516px;top:4655px;width:168px;height:47px;font-size:17px">View Programs</div>

<!-- Footer -->
<footer class="abs footer">
  <div class="logo">THE WELLNESS<br>BARN</div>
  <h4 style="left:430px;top:52px">CONTACT US</h4>
  <div class="contact-row" style="top:100px"><span class="ic"><svg width="14" height="14" viewBox="0 0 24 24" fill="#1f3a1e"><path d="M12 2a7 7 0 0 0-7 7c0 5 7 13 7 13s7-8 7-13a7 7 0 0 0-7-7zm0 9.5A2.5 2.5 0 1 1 12 6.5a2.5 2.5 0 0 1 0 5z"/></svg></span><span>48 Timber Lane, Cedar Bay,<br>Australia, 4000.</span></div>
  <div class="contact-row" style="top:162px"><span class="ic"><svg width="14" height="14" viewBox="0 0 24 24" fill="#1f3a1e"><path d="M5 3h4l2 5-2.5 1.5a11 11 0 0 0 6 6L16 13l5 2v4a2 2 0 0 1-2 2A16 16 0 0 1 3 5a2 2 0 0 1 2-2z"/></svg></span><span>Call Us<br>+61 7 5550 1234</span></div>
  <div class="contact-row" style="top:224px"><span class="ic"><svg width="14" height="14" viewBox="0 0 24 24" fill="#1f3a1e"><path d="M2 5h20v14H2zM2 5l10 8 10-8" stroke="#d9d6cb" stroke-width="1.5"/></svg></span><span>Email Us<br>hello@wellnessbarncedarbay.com</span></div>
  <h4 style="left:738px;top:52px">STAY UPDATED</h4>
  <p class="news">Subscribe Newsletter for the latest healthtips and program updates.</p>
  <div class="email">Enter Your Email</div>
  <div class="sub">SUBSCRIBE</div>
  <hr>
  <div class="legal">Terms and Conditions &nbsp;&nbsp;|&nbsp;&nbsp; Privacy Policy &nbsp;&nbsp;|&nbsp;&nbsp; © 2025 The Wellness Barn Cedar Bay. All rights reserved.</div>
</footer>

</body>
</html>
```